Accounting firm needing business card / letterhead designed
Marcus L. Trenholm, CPA
marcus@veltrowledger.com
www.veltrowledger.com
842 E Alder Ave Harlow Bend, WI 43827
419-562-0974

```html
<!DOCTYPE html>
<html lang="en">
<head>
<meta charset="utf-8">
<title>Veltrow Ledger – Business Card</title>
<link href="https://fonts.googleapis.com/css2?family=Open+Sans:wght@400;600;700&display=swap" rel="stylesheet">
<style>
  :root {
    --backdrop: #8f8f8f;
    --navy: #262262;
    --lime: #8dc63f;
    --paper: #ffffff;
    --ink: #262262;
  }
  html, body {
    margin: 0;
    padding: 0;
    width: 1200px;
    height: 900px;
    overflow: hidden;
    background: var(--backdrop);
    font-family: "Open Sans", Arial, sans-serif;
  }
  .stage {
    position: relative;
    width: 1200px;
    height: 900px;
  }
  .card {
    position: absolute;
    top: 306px;
    width: 439px;
    height: 272px;
    overflow: hidden;
  }
  .card-front { left: 149px; background: var(--paper); }
  .card-back { left: 609px; background: var(--navy); }

  .front-shapes {
    position: absolute;
    inset: 0;
  }
  .holder-name {
    position: absolute;
    left: 36px;
    top: 35px;
    margin: 0;
    font-size: 15.5px;
    font-weight: 600;
    color: var(--ink);
    letter-spacing: 0.2px;
    text-transform: uppercase;
  }
  .wordmark {
    position: absolute;
    margin: 0;
    font-weight: 700;
    font-size: 31px;
    letter-spacing: 2px;
    line-height: 1;
    white-space: nowrap;
    text-transform: uppercase;
  }
  .card-front .wordmark {
    right: 24px;
    top: 116px;
    color: var(--navy);
  }
  .card-back .wordmark {
    left: 0;
    right: 0;
    top: 118px;
    text-align: center;
    color: var(--paper);
  }
  .contact-list {
    position: absolute;
    left: 27px;
    top: 186px;
    margin: 0;
    padding: 0;
    list-style: none;
    font-size: 12px;
    color: var(--ink);
  }
  .contact-list li {
    display: flex;
    align-items: center;
    height: 16px;
  }
  .contact-list svg {
    width: 10px;
    height: 10px;
    margin-right: 5px;
    fill: var(--ink);
  }
  .address {
    position: absolute;
    right: 23px;
    top: 202px;
    margin: 0;
    font-style: normal;
    font-size: 12px;
    line-height: 16px;
    text-align: right;
    color: var(--ink);
  }
</style>
</head>
<body>
<main class="stage">
  <section class="card card-front" aria-label="Business card front">
    <svg class="front-shapes" width="439" height="272" viewBox="0 0 439 272" aria-hidden="true">
      <polygon points="0,26 13,26 16,63 0,63" fill="var(--lime)"/>
      <polygon points="11,26 29,26 29,63 15,63" fill="var(--navy)"/>
      <polygon points="0,252 216,252 209,272 0,272" fill="var(--lime)"/>
      <polygon points="220,243 439,243 439,272 209,272" fill="var(--navy)"/>
    </svg>

    <h1 class="holder-name">Marcus L. Trenholm, CPA</h1>

    <p class="wordmark">Veltrow Ledger</p>

    <ul class="contact-list">
      <li>
        <svg viewBox="0 0 10 10" aria-hidden="true"><path d="M2 0.5 L3.6 2.6 L2.7 3.6 C3.3 5 4.9 6.7 6.4 7.3 L7.4 6.4 L9.5 8 L8.4 9.5 C4.4 9.3 0.7 5.6 0.5 1.6 Z"/></svg>
        555-562-0974
      </li>
      <li>
        <svg viewBox="0 0 10 10" aria-hidden="true"><path d="M0.5 2 H9.5 V8.5 H0.5 Z" fill="var(--ink)"/><path d="M1 2.6 L5 5.6 L9 2.6" stroke="#fff" stroke-width="0.8" fill="none"/></svg>
        marcus@veltrowledger.com
      </li>
      <li>
        <svg viewBox="0 0 10 10" aria-hidden="true"><circle cx="5" cy="5" r="4.5"/><path d="M1 4.5 H9 M5 0.8 C3 3 3 7 5 9.2 M5 0.8 C7 3 7 7 5 9.2" stroke="#fff" stroke-width="0.6" fill="none"/></svg>
        www.veltrowledger.com
      </li>
    </ul>

    <address class="address">842 E Alder Ave Harlow Bend,<br>WI 43827</address>
  </section>

  <section class="card card-back" aria-label="Business card back">
    <p class="wordmark">Veltrow Ledger</p>
  </section>
</main>
</body>
</html>
```